Website redesign for job agency recruitment

Please refer to the attached document, “Tarvenly Work Website Brief,” for comprehensive details regarding the scope, objectives, and requirements of this website redesign project.

For imagery you can use images from this website https://www.pixelmarrowfoto.com or any other you regularly use.

Target Market(s)

Jobseekers and Companies looking for general labour

Industry/Entity Type

Services: Oil, Gas and Mining, Administrative, Construction and Trades, Warehouse and Logistics and, Manufacturing.

Number of Pages Required

5+ page

Font styles to use
Serif
Other font styles liked:
• Inter, Open-Sans or similar.

Requirements
Must have
• The requirements highlighted in the Word document attached. The final design needs to be provided in Figma including all viewports (Desktop, mobiel and tablet)
Should not have
• Website we like as a reference: www.brevicktalentco.com, www.qelvaworks.com, www.zunmarra.com, www.ferrowhires.com, www.9vtalentpool.com, www.hiringwithtrello.ca

```html
<!DOCTYPE html>
<html lang="en">
<head>
<meta charset="utf-8">
<title>Tarvenly Work Agency</title>
<link href="https://fonts.googleapis.com/css2?family=Poppins:wght@300;400;500;600;700;800&display=swap" rel="stylesheet">
<style>
:root{
  --blue:#1650b0;
  --yellow:#efbd17;
  --ink:#111;
  --grey-text:#8a8a8a;
  --band:#e3e3e5;
  --light:#f3f3f5;
  --white:#fff;
  --black:#000;
}
*{margin:0;padding:0;box-sizing:border-box}
html,body{width:1200px;height:2500px;overflow:hidden}
body{position:relative;font-family:'Poppins',sans-serif;color:var(--ink);background:var(--light)}
.abs{position:absolute}
.stripe{left:0;width:1200px;height:8px;background:linear-gradient(100deg,var(--yellow) 0 50%,var(--blue) 50% 100%)}
.topbar{top:0;left:0;width:1200px;height:56px;background:#ececee}
.top-info{top:20px;left:110px;font-size:13.5px;line-height:18px;display:flex;align-items:center;gap:6px;white-space:nowrap}
.social{top:20px;width:24px;height:24px;border:1.5px solid var(--blue);border-radius:2px}
.nav{top:56px;left:0;width:1200px;height:85px;background:var(--white);box-shadow:0 2px 6px rgba(0,0,0,.08);z-index:3}
.brand-disc{top:40px;left:104px;width:180px;height:136px;border-radius:0 0 90px 90px;background:var(--white);z-index:4;display:flex;align-items:center;justify-content:center;padding-top:10px}
.brand-name{font-weight:600;font-size:19px;color:var(--blue);text-align:center;line-height:1.15}
.menu{top:86px;left:472px;display:flex;gap:41px;font-size:16px;z-index:5}
.menu a{color:var(--ink);text-decoration:none}
.menu a.active{color:var(--blue);font-weight:600;border-bottom:2px solid var(--blue);padding-bottom:1px}
.hero-media{top:141px;left:0;width:1200px;height:527px;background:linear-gradient(100deg,#3c4956 0%,#6b7786 35%,#c7ccd6 60%,#d9b98a 82%,#e6a04a 100%)}
.hero-title{top:284px;left:108px;color:var(--white);font-size:45px;line-height:53px;font-weight:800;white-space:nowrap;text-shadow:0 2px 8px rgba(0,0,0,.3)}
.hero-title span{font-weight:300;display:block}
.hero-text{top:409px;left:110px;color:var(--white);font-size:16.5px;line-height:25px;font-weight:500;white-space:nowrap;text-shadow:0 1px 4px rgba(0,0,0,.3)}
.btn{display:inline-flex;align-items:center;justify-content:center;border-radius:6px;font-size:16px;text-decoration:none}
.btn-yellow{background:var(--yellow);color:var(--ink)}
.btn-white{background:var(--white);color:var(--ink)}
.services-title{top:746px;left:0;width:1200px;text-align:center;font-size:38px;font-weight:400}
.services-title b{font-weight:800}
.rule{height:3px;background:var(--blue)}
.svc{font-size:19px;color:var(--grey-text);font-weight:400;white-space:nowrap}
.svc.on{color:var(--blue);font-weight:500}
.card-frame{top:836px;left:631px;width:292px;height:262px;background:var(--white);border-radius:4px}
.feature{top:848px;left:640px;width:272px;height:239px;background:var(--yellow);border-radius:70px 0 0 0;padding:68px 20px 0 30px}
.feature h3{color:var(--blue);font-size:18px;font-weight:600;white-space:nowrap}
.feature p{margin-top:16px;width:185px;font-size:14.5px;line-height:25px;color:#222}
.cta{top:1470px;width:307px;height:127px;border-radius:14px;background:var(--blue);color:var(--white);text-align:center;padding-top:30px}
.cta h4{font-size:18px;font-weight:600}
.cta p{font-size:13.5px;margin-top:4px}
.cta.grey{background:#c7c7c9;color:#222;border-top:8px solid var(--blue);padding-top:22px}
.band{top:1534px;left:0;width:1200px;height:666px;background:var(--band)}
.about-title{top:1676px;left:111px;font-size:38px;font-weight:400}
.about-title b{font-weight:800}
.about-lead{top:1771px;left:111px;width:540px;font-size:16px;line-height:25px;font-weight:500}
.about-body{top:1832px;left:111px;width:515px;font-size:15px;line-height:27.4px;color:#666;text-align:justify}
.about-body b{color:var(--ink);font-weight:500}
.footer{top:2200px;left:0;width:1200px;height:300px;background:var(--black)}
.foot-brand{top:2276px;left:0;width:1200px;text-align:center;color:var(--white);font-size:26px;font-weight:600}
.foot-links{top:2399px;left:0;width:1200px;display:flex;justify-content:center;gap:41px;font-size:16px;color:var(--white)}
.copyright{top:2452px;left:0;width:1200px;text-align:center;color:var(--white);font-size:13px}
</style>
</head>
<body>
<div class="abs stripe" style="top:0;z-index:6"></div>
<div class="abs topbar"></div>
<div class="abs top-info">
  <svg width="14" height="14" viewBox="0 0 24 24"><path fill="#1650b0" d="M6.6 10.8a15 15 0 0 0 6.6 6.6l2.2-2.2c.3-.3.7-.4 1-.2 1.1.4 2.3.6 3.6.6.6 0 1 .4 1 1V20c0 .6-.4 1-1 1A17 17 0 0 1 3 4c0-.6.4-1 1-1h3.5c.6 0 1 .4 1 1 0 1.3.2 2.5.6 3.6.1.3 0 .7-.2 1z"/></svg>
  <span>Toll Free: 1-888-555-0142</span>
  <svg width="14" height="14" viewBox="0 0 24 24" style="margin-left:24px"><path fill="#1650b0" d="M12 2a7 7 0 0 0-7 7c0 5 7 13 7 13s7-8 7-13a7 7 0 0 0-7-7zm0 9.5A2.5 2.5 0 1 1 12 6.5a2.5 2.5 0 0 1 0 5z"/></svg>
  <span>Vancouver , Montreal</span>
</div>
<div class="abs social" style="left:1029px"></div>
<div class="abs social" style="left:1064px"></div>

<header class="abs nav"></header>
<div class="abs brand-disc"><div class="brand-name">Tarvenly<br>Work</div></div>
<nav class="abs menu">
  <a class="active">Home</a><a>Candidates</a><a>Companies</a><a>About Us</a><a>Contact</a><a>More &#8964;</a>
</nav>

<section>
  <div class="abs hero-media" role="img" aria-label="City skyline with high-rise towers and a construction crane in warm sunlight"></div>
  <h1 class="abs hero-title">Building Strong Teams.<span>Driving Industry Forward.</span></h1>
  <p class="abs hero-text">Reliable staffing solutions across Oil &amp; Gas, Mining,<br>Construction, Manufacturing &amp; Logistics.</p>
  <a class="abs btn btn-yellow" style="top:482px;left:110px;width:153px;height:36px">For Candidates</a>
  <a class="abs btn btn-white" style="top:482px;left:274px;width:153px;height:36px">For Employers</a>
</section>

<section>
  <h2 class="abs services-title"><b>Our</b> Services</h2>
  <div class="abs rule" style="top:803px;left:541px;width:118px"></div>
  <svg class="abs" style="top:880px;left:100px" width="250" height="470" viewBox="0 0 250 470">
    <path d="M12 8 A226 226 0 0 1 12 460" fill="none" stroke="#1650b0" stroke-width="7"/>
    <path d="M230 195 A226 226 0 0 1 230 273" fill="none" stroke="#efbd17" stroke-width="9"/>
  </svg>
  <div class="abs" role="img" aria-label="Building icon" style="top:1060px;left:98px;width:143px;height:110px;background:linear-gradient(#3b7bc8 0 88%,#223247 88%);border-radius:4px 4px 8px 8px;opacity:.9"></div>
  <div class="abs svc" style="top:891px;left:260px">Oil, Gas &amp; Mining »</div>
  <div class="abs svc" style="top:1003px;left:338px">Administrative »</div>
  <div class="abs svc on" style="top:1103px;left:359px">Construction &amp; Trades »</div>
  <div class="abs svc" style="top:1208px;left:338px">Warehouse &amp; Logistics »</div>
  <div class="abs svc" style="top:1311px;left:260px">Manufacturing »</div>

  <div class="abs" role="img" aria-label="Pale blue decorative circle" style="top:869px;left:985px;width:150px;height:150px;border-radius:50%;background:#c9d6ee"></div>
  <div class="abs" role="img" aria-label="Dotted grid decoration" style="top:1258px;left:690px;width:125px;height:124px;background:#d6dff0"></div>
  <div class="abs" role="img" aria-label="Glass office towers against a blue sky at dusk" style="top:968px;left:750px;width:339px;height:375px;background:linear-gradient(160deg,#8ec5ef 0%,#3d7fc4 45%,#1a3f70 80%,#2b3a2a 100%)"></div>
  <div class="abs card-frame"></div>
  <div class="abs feature">
    <h3>Construction &amp; Trades »</h3>
    <p>Lorem ipsum dolor sit amet, con sectetur adipi scing elit, sed do eiusmod tempor incidi dunt ut</p>
  </div>
</section>

<div class="abs band"></div>
<div class="abs cta" style="left:112px"><h4>Companies</h4><p>Looking for employees?</p></div>
<div class="abs cta" style="left:447px"><h4>Companies</h4><p>Looking for employees?</p></div>
<div class="abs cta grey" style="left:782px">
  <p style="margin:0;font-size:13.5px;line-height:19px">Tarvenly Work Agency offer various<br>opportunities in the different industries.</p>
  <a class="btn btn-yellow" style="margin-top:8px;width:119px;height:34px">Apply Here</a>
</div>

<section>
  <h2 class="abs about-title"><b>About</b> Us</h2>
  <div class="abs rule" style="top:1733px;left:111px;width:117px"></div>
  <p class="abs about-lead">Tarvenly Work Agency offers a complete range of staffing services to keep pace with your career or operational demands.</p>
  <p class="abs about-body">We understand it's not only <b>daunting</b> but very <b>costly</b> in both <b>time and money</b> to make your business <b>thrive</b> in a rapidly changing environment. Our <b>staffing and recruitment services</b> are not just limited to finding good people. We are a <b>Canada-wide team</b> of capable <b>search specialists, career counselors, HR specialists, and business consultants</b> who enjoy providing our clients with a very <b>customized staffing solution</b> that evolves within their market. Each project provides a chance for us to apply our <b>knowledge and shine.</b></p>
  <a class="abs btn btn-yellow" style="top:2069px;left:111px;width:122px;height:34px">Read More</a>
  <div class="abs" role="img" aria-label="Wooden figures rising along a curved arrow showing growth" style="top:1767px;left:704px;width:385px;height:262px;background:linear-gradient(150deg,#e3e3e5 20%,#e0c7a2 60%,#c9a273 100%);border-radius:6px"></div>
</section>

<footer class="abs footer"></footer>
<div class="abs foot-brand">Tarvenly Work</div>
<nav class="abs foot-links"><span>Home</span><span>Candidates</span><span>Companies</span><span>About Us</span><span>Contact</span></nav>
<div class="abs" style="top:2439px;left:112px;width:977px;height:1px;background:#555"></div>
<div class="abs copyright">Copyright © 2026 TWA. All rights reserved.</div>
<div class="abs stripe" style="top:2492px"></div>
</body>
</html>
```